Garden Design Flier

I would like a PDF of this half page A4 flier in soft green tones with dark green leaves.

Target Market(s)

Home owners and real estate agents

Font styles to use
Serif
Other font styles liked:
• Papyrus

Colors
acd136
9bcb3c
cadf82
fefdec

Requirements
Must have
• Green tones
Nice to have
• Leaves, vines, lawns
Should not have
• Open to ideas, but classic style

```html
<!DOCTYPE html>
<html lang="en">
<head>
<meta charset="utf-8">
<title>Heirloom Gardens – Flier</title>
<link rel="stylesheet" href="https://fonts.googleapis.com/css2?family=Open+Sans:wght@700&family=Source+Sans+3:wght@400;600&display=swap">
<style>
  :root {
    --page-bg: #ffffff;
    --frame-line: #8a8a8a;
    --ink: #111111;
    --green-deep: #63b347;
    --green-soft: #8fc85e;
    --green-icon: #1a7a45;
    --green-art: #d6ecc9;
  }
  html, body {
    margin: 0;
    padding: 0;
    width: 1200px;
    height: 1100px;
    overflow: hidden;
    background: var(--page-bg);
  }
  .canvas {
    position: relative;
    width: 1198px;
    height: 1098px;
    border: 1px solid var(--frame-line);
  }
  .flier {
    position: absolute;
    left: 356px;
    top: 220px;
    width: 483px;
    height: 682px;
    overflow: hidden;
    background: var(--page-bg);
    outline: 1px solid var(--frame-line);
  }
  .flier svg { display: block; }
  .wave-deep { fill: var(--green-deep); }
  .wave-soft { fill: var(--green-soft); }
  .vine-art { fill: var(--green-art); }
  .text { font-family: "Source Sans 3", "Myriad Pro", sans-serif; fill: var(--ink); }
  .brand-title { font-size: 58px; letter-spacing: 0.5px; }
  .brand-sub { font-size: 22px; }
  .byline { font-size: 19px; }
  .credential { font-size: 12px; }
  .services { font-family: "Open Sans", Verdana, sans-serif; font-weight: 700; font-size: 17px; fill: var(--ink); }
  .blurb { font-size: 10.4px; }
  .contact { font-size: 12px; }
  .icon-disc { fill: var(--green-icon); }
  .icon-line { fill: none; stroke: #ffffff; stroke-width: 1; }
  .icon-phone { fill: var(--green-icon); }
</style>
</head>
<body>
<div class="canvas">
  <div class="flier">
    <svg width="483" height="682" viewBox="0 0 483 682" xmlns="http://www.w3.org/2000/svg">
      <g class="waves">
        <path class="wave-deep" d="M0,180 C60,245 82,330 78,405 C72,520 140,600 227,600 C270,600 305,585 331,557 C380,510 430,480 483,468 L483,682 L0,682 Z"/>
        <path class="wave-soft" d="M0,218 C40,262 60,310 57,364 C55,430 55,520 90,560 C105,580 120,598 137,607 C160,620 185,622 202,618 C250,612 295,598 328,581 C290,620 245,643 197,643 C150,643 100,620 72,594 C45,560 42,500 36,435 C30,380 18,340 0,319 Z"/>
        <path class="wave-soft" d="M483,514 C445,523 420,537 402,557 C375,588 350,612 320,632 C290,652 250,662 220,667 C245,670 258,670 268,670 C330,668 380,645 405,605 C425,585 455,570 483,563 Z"/>
      </g>

      <rect class="vine-art" x="324" y="366" width="146" height="100" rx="18" role="img" aria-label="Illustration of a curling green vine with leaves"/>

      <g class="text">
        <text class="brand-title" x="242" y="161" text-anchor="middle">HEIRLOOM</text>
        <text class="brand-sub" x="245" y="201" text-anchor="middle">GARDENS</text>
        <text class="byline" x="243" y="237" text-anchor="middle">by Ewan Hartley</text>
        <text class="credential" x="246" y="264" text-anchor="middle">Certificate 3. Horticulture.Vale Institute</text>
      </g>

      <text class="services" x="111" y="297" textLength="273" lengthAdjust="spacing">Design  Instal  Grow Tend  Enjoy</text>

      <g class="text blurb">
        <text x="111" y="331">All your Gardening and landscaping needs from design</text>
        <text x="111" y="344">and installation to general maintenance.</text>
        <text x="111" y="356">Bespoke vegetable gardens and potager designs created</text>
        <text x="111" y="369">to suite your site and requirements.</text>
      </g>

      <g class="contact-list">
        <g class="icon-web">
          <circle class="icon-disc" cx="121" cy="399" r="9.5"/>
          <circle class="icon-line" cx="121" cy="399" r="4.5"/>
          <ellipse class="icon-line" cx="121" cy="399" rx="2" ry="4.5"/>
          <line class="icon-line" x1="116.5" y1="399" x2="125.5" y2="399"/>
        </g>
        <path class="icon-phone" d="M115,417 C116,416 118,415 119,416 L121,420 C121,421 120,422 119,422 C119,424 121,427 123,428 C124,427 125,426 126,427 L128,429 C128,431 126,432 125,432 C119,431 114,424 115,417 Z"/>
        <g class="text contact">
          <text x="139" y="400">ewan@heirloomgardens.com.au</text>
          <text x="139" y="428">0491-570156</text>
          <text x="139" y="459">ABN:12345678901</text>
        </g>
      </g>
    </svg>
  </div>
</div>
</body>
</html>
```